IT Freelancer (Consulting, trainer and project manager) needed letterhead

As a freelancer for IT Trainingswhip, consulting and project management I need a letterhead design. What is desired is a design that fits the existing logo (see Annex). It is functional, reliable, and equal time wirkenn Agil and modern. The whole is in color, as well as printed out to make a good impression on a black and white printer. The whole is to the existing Cooperate design (business card, homepage, logo) fit. Therefore, the choice of colors.
Updates

Target Market(s)

Customers such as medium-sized enterprises, training institutions

Industry/Entity Type

Consulting

Colors
0455a3
3277b5
85abd2
cfdfed
34a6d7
32a6d6
249fd4
0792cd
85cae6

Requirements
Must have
• Must include logo (see Annex) address (Brunnerweg 14, 95617 Waldsassen, Germany). Must seriously and act simultaneously Agil. Design should (even) be adaptable (signature, address, etc.) design must look good on a black / white laser

```html
<!DOCTYPE html>
<html lang="de">
<head>
<meta charset="utf-8">
<title>Lukas Brenner – Briefbogen</title>
<link href="https://fonts.googleapis.com/css2?family=Lato:wght@400;700;900&display=swap" rel="stylesheet">
<style>
  :root {
    --navy: #0455a3;
    --mid: #3277b5;
    --sky: #249fd4;
    --cyan: #34c7ea;
    --pale: #85cae6;
    --mist: #f3f4f5;
    --paper: #ffffff;
    --stage: #bdbdbd;
    --ink: #222222;
  }
  * { box-sizing: border-box; margin: 0; padding: 0; }
  html, body { width: 1200px; height: 1002px; overflow: hidden; }
  body {
    background: var(--stage);
    font-family: "Lato", Arial, sans-serif;
    position: relative;
  }
  .letterhead {
    position: absolute;
    left: 270px; top: 34px;
    width: 660px; height: 934px;
    background: var(--paper);
    box-shadow: 0 6px 22px rgba(0,0,0,.25);
    overflow: hidden;
  }
  .edge-marks { position: absolute; left: 0; top: 0; width: 12px; }
  .edge-marks span { display: block; width: 12px; margin-bottom: 5px; }
  .edge-marks .m1 { height: 58px; background: var(--navy); }
  .edge-marks .m2 { height: 40px; background: var(--sky); }
  .edge-marks .m3 { height: 30px; background: var(--cyan); }
  .edge-marks .m4 { height: 16px; background: var(--pale); }
  .sender-line {
    position: absolute; left: 52px; top: 128px;
    font-size: 8px; color: var(--ink); letter-spacing: .1px; white-space: nowrap;
  }
  .brand {
    position: absolute; right: 40px; top: 92px;
    display: flex; flex-direction: column; align-items: center; gap: 8px;
  }
  .brand-dot { width: 72px; height: 72px; border-radius: 50%; background: var(--navy); }
  .brand-name {
    font-weight: 900; font-size: 16px; letter-spacing: 1.5px;
    color: var(--navy); text-transform: uppercase; text-align: center; line-height: 1.1;
  }
  .backdrop {
    position: absolute; left: 110px; top: 390px;
    width: 440px; height: 440px; border-radius: 50%;
    background: var(--mist);
  }
  .footer {
    position: absolute; left: 0; right: 0; bottom: 0; height: 64px;
    background: var(--navy);
    color: #fff; text-align: center;
    padding-top: 14px;
  }
  .footer::before {
    content: ""; position: absolute; left: 0; right: 0; top: -9px;
    height: 2px; background: var(--sky);
  }
  .footer .address { font-size: 12px; margin-bottom: 5px; }
  .footer .contacts { font-size: 12px; display: flex; justify-content: center; gap: 14px; white-space: nowrap; }
  .footer .contacts span { display: inline-flex; align-items: center; gap: 4px; }
  .footer svg { width: 10px; height: 10px; fill: var(--pale); }
</style>
</head>
<body>
  <div class="letterhead">
    <div class="edge-marks"><span class="m1"></span><span class="m2"></span><span class="m3"></span><span class="m4"></span></div>

    <p class="sender-line">Lukas Brenner · Brunnerweg 14 · 95617 Mooshain · Germany</p>

    <div class="brand">
      <div class="brand-dot"></div>
      <div class="brand-name">Lukas<br>Brenner</div>
    </div>

    <div class="backdrop" role="img" aria-label="Faint brand emblem watermark"></div>

    <footer class="footer">
      <p class="address">Brunnerweg 14, 95617 Mooshain, Germany</p>
      <p class="contacts">
        <span><svg viewBox="0 0 10 10"><path d="M2 0l2 2-1 2c1 1 2 2 3 3l2-1 2 2-2 2C4 10 0 6 0 2z"/></svg>512 004 2700</span>
        <span><svg viewBox="0 0 10 10"><rect x="2" y="0" width="6" height="3"/><rect x="0" y="3" width="10" height="5"/><rect x="2" y="7" width="6" height="3"/></svg>512 004 2701</span>
        <span><svg viewBox="0 0 10 10"><path d="M0 2h10v6H0z M0 2l5 3 5-3" /></svg>info@lukasbrenner.de</span>
        <span><svg viewBox="0 0 10 10"><circle cx="5" cy="5" r="5"/></svg>www.lukasbrenner.de</span>
      </p>
    </footer>
  </div>
</body>
</html>
```